Plakat für Hersteller von maßgefertigten Tischunikaten aus Massivholz
Zielgruppe
Wir sind einen Firma die sich auf die Fertigung von maßgefertigten Tischunikaten aus Massivholz spezialisiert hat. Unsere Zielgruppe sind Design affine Leute, im Alter von 35-55 Jahren
Aufgabenstellung
Wir benötigen das Design für eine Messewand mit den Maßen 443X227 cm. 5 Zentimeter rundlaufen dürfen keine Elemente mehr platziert werden. Die Messewand steht im Hintergrund von unserem Stand bei verschiedenen Designmessen
Infos die auf die Messewand müssen: Logo, Tischmanufaktur aus Stuttgart, Maßgefertigte Tischunikate (Bei der Formulierung bin ich flexibel, ihr könnt bspw. auch nur Stichworte benutzen, aber Stuttgart und maßgefertigt ist wichtig).
Die Messewand soll sehr minimalistisch gestaltet sein, bei der letzten Messewand hatten wir ein Foto von einem Tisch im Hintergrund und das sah merkwürdig aus.

```html
<!DOCTYPE html>
<html lang="de">
<head>
<meta charset="utf-8">
<title>Messewand – Lindgart Manufaktur</title>
<link rel="stylesheet" href="https://fonts.googleapis.com/css2?family=Oswald:wght@600;700&family=Montserrat:wght@300;500;700&display=swap">
<style>
  :root {
    --page-bg: #efece6;
    --wall-black: #1c1c1c;
    --wall-black-light: #2b2b2b;
    --text-light: #dcdcdc;
    --wood-light: #e6d6bf;
    --wood-mid: #cdb393;
    --wood-dark: #a88a66;
  }
  * { margin: 0; padding: 0; box-sizing: border-box; }
  html, body {
    width: 1200px;
    height: 1117px;
    overflow: hidden;
    background: var(--page-bg);
  }
  .trade-wall {
    position: absolute;
    left: 20px;
    top: 261px;
    width: 1160px;
    height: 594px;
    overflow: hidden;
    background:
      radial-gradient(ellipse at 25% 30%, var(--wall-black-light) 0%, transparent 60%),
      var(--wall-black);
  }
  .wood-feature {
    position: absolute;
    left: 480px;
    top: 0;
    width: 680px;
    height: 594px;
    background:
      radial-gradient(ellipse 62% 68% at 58% 52%, var(--wall-black) 0%, var(--wall-black) 55%, var(--wood-dark) 72%, var(--wood-mid) 84%, var(--wood-light) 100%);
    -webkit-mask-image: linear-gradient(90deg, transparent 0%, #000 18%);
    mask-image: linear-gradient(90deg, transparent 0%, #000 18%);
  }
  .headline {
    position: absolute;
    left: 68px;
    top: 128px;
    color: var(--text-light);
    font-family: "Oswald", sans-serif;
    text-transform: uppercase;
    line-height: 1;
  }
  .headline__kicker {
    display: block;
    font-weight: 600;
    font-size: 56px;
    letter-spacing: -0.5px;
  }
  .headline__city {
    display: block;
    margin-top: 8px;
    font-weight: 700;
    font-size: 84px;
    letter-spacing: -1px;
  }
  .claim-band {
    position: absolute;
    left: 0;
    top: 336px;
    width: 419px;
    height: 67px;
    border-top: 2px solid var(--text-light);
    border-bottom: 2px solid var(--text-light);
    display: flex;
    align-items: center;
    padding-left: 68px;
  }
  .claim-band__text {
    font-family: "Montserrat", sans-serif;
    font-weight: 700;
    font-size: 25px;
    letter-spacing: 0.42em;
    color: var(--text-light);
    text-transform: uppercase;
  }
  .social-handle {
    position: absolute;
    left: 68px;
    top: 477px;
    display: flex;
    align-items: center;
    gap: 12px;
    color: var(--text-light);
    font-family: "Montserrat", sans-serif;
    font-weight: 300;
    font-size: 19px;
    letter-spacing: 0.22em;
    text-transform: uppercase;
  }
  .social-handle__marker {
    width: 26px;
    height: 26px;
    border: 2px solid var(--text-light);
    border-radius: 6px;
  }
  .brand-name {
    position: absolute;
    left: 829px;
    top: 290px;
    transform: translateX(-50%);
    display: flex;
    align-items: center;
    gap: 14px;
    white-space: nowrap;
    color: var(--text-light);
    font-family: "Montserrat", sans-serif;
    font-weight: 500;
    font-size: 22px;
    letter-spacing: 0.3em;
    text-transform: uppercase;
  }
  .brand-name__dot {
    width: 16px;
    height: 16px;
    border-radius: 50%;
    background: var(--text-light);
  }
</style>
</head>
<body>
  <main class="trade-wall">
    <div class="wood-feature" role="img" aria-label="Helle Holzmaserung als großflächiges Gestaltungselement"></div>

    <h1 class="headline">
      <span class="headline__kicker">Tischmanufaktur</span>
      <span class="headline__city">Aus Stuttgart</span>
    </h1>

    <div class="claim-band">
      <p class="claim-band__text">Maßgefertigt</p>
    </div>

    <p class="social-handle">
      <span class="social-handle__marker" aria-hidden="true"></span>
      lindgart_manufaktur
    </p>

    <p class="brand-name">
      <span class="brand-name__dot" aria-hidden="true"></span>
      Lindgart Manufaktur
    </p>
  </main>
</body>
</html>
```